Bespoke Builders Business Card Design

We need a business card for an established builder of high quality bespoke homes in Auckland and Northland. We build and renovate homes collaboratively facilitating effective communication between owners, builders, architects, suppliers and tradespeople. We have never built or renovated a home that leaks or has faults. We only use reliable materials. We have never been sued or had legal action taken against us. We are honest builders of bespoke homes not group mass produced homes. Our niche market is in character homes. We practice sustainability and have built a lot of coastal property. We have been in business for over thirty years . We would like to see natural colors of the environment sand,sea and maybe vegetation . The design should communicate quality, sustainability,fair pricing, open communication and the originality of bespoke building. And the fact that the builder is registered.

Industry/Entity Type

Business

Contact Information for Business Card

Rowan Tellick Builders
Ph. 021583917
18 Kestrel Rd Harwood Bay Auckland 0814
PO Box 927 Mangawhai 0583

```html
<!DOCTYPE html>
<html lang="en">
<head>
<meta charset="utf-8">
<title>Rowan Tellick Builders – Business Card</title>
<link href="https://fonts.googleapis.com/css2?family=Bodoni+Moda:wght@700&family=PT+Sans:wght@400&display=swap" rel="stylesheet">
<style>
  :root {
    --page-bg: #ebe6de;
    --card-white: #f4f4f6;
    --card-navy: #2c3283;
    --card-black: #050505;
    --name-ink: #141414;
    --name-light: #f2f2f2;
    --contact-ink: #dcdcf4;
    --shadow: rgba(40, 30, 20, 0.28);
  }
  * { box-sizing: border-box; margin: 0; padding: 0; }
  html, body {
    width: 1200px;
    height: 902px;
    overflow: hidden;
    background: var(--page-bg);
  }
  .sheet {
    width: 1200px;
    height: 902px;
    display: flex;
    align-items: center;
    justify-content: center;
    gap: 40px;
  }
  .card {
    position: relative;
    width: 540px;
    height: 309px;
    overflow: hidden;
    box-shadow: 0 10px 26px var(--shadow);
  }
  .card-back {
    background: var(--card-black);
    border: 5px solid var(--card-navy);
    display: flex;
    align-items: center;
    justify-content: center;
  }
  .card-back .company-name {
    color: var(--name-light);
    text-shadow: 0 0 4px rgba(255, 255, 255, 0.55);
  }
  .card-front { background: var(--card-white); }
  .card-front .wave {
    position: absolute;
    inset: 0;
    width: 100%;
    height: 100%;
  }
  .card-front .wave path { fill: var(--card-navy); }
  .company-name {
    font-family: "Bodoni Moda", "Didot", serif;
    font-weight: 700;
    font-size: 35px;
    letter-spacing: 0.5px;
    white-space: nowrap;
  }
  .card-front .company-name {
    position: absolute;
    top: 58px;
    left: 0;
    right: 0;
    text-align: center;
    color: var(--name-ink);
    padding-left: 60px;
  }
  .contact {
    position: absolute;
    right: 34px;
    bottom: 34px;
    width: 360px;
    text-align: center;
    font-family: "PT Sans", "Myriad Pro", sans-serif;
    font-size: 16.5px;
    line-height: 1.3;
    color: var(--contact-ink);
  }
</style>
</head>
<body>
  <main class="sheet">
    <section class="card card-back" aria-label="Business card back">
      <h2 class="company-name">Rowan Tellick Builders</h2>
    </section>

    <section class="card card-front" aria-label="Business card front">
      <svg class="wave" viewBox="0 0 540 309" preserveAspectRatio="none" aria-hidden="true">
        <path d="M0 228 Q330 212 540 52 L540 309 L0 309 Z"/>
      </svg>
      <h1 class="company-name">Rowan Tellick Builders</h1>
      <address class="contact">
        <p class="phone">021583917</p>
        <p class="street">18 Kestrel Rd Harwood Bay Auckland 0814</p>
        <p class="po-box">PO Box 927 Mangawhai 0583</p>
      </address>
    </section>
  </main>
</body>
</html>
```